Varden Clinical new year card

Hi,
I would like a New Year greetings card to send to my customers.

If you need to look at our logo : www.vardenclinical.com

If you want to play with images of our device, see
quilotherapy.ca

The goal is to have a card to wish a happy new year and we look forward collaborating with them in the new year.

```html
<!DOCTYPE html>
<html lang="en">
<head>
<meta charset="UTF-8">
<title>Varden Clinical – Happy New Year 2022</title>
<link rel="stylesheet" href="https://fonts.googleapis.com/css2?family=Archivo+Black&family=Great+Vibes&family=Roboto+Condensed:wght@500&family=Open+Sans:wght@700&display=swap">
<style>
  :root {
    --backdrop: #623f1c;
    --card-light: #f4efe8;
    --card-warm: #eadccb;
    --script-brown: #8a5526;
    --year-red: #bf3a25;
    --brand-grey: #5f6066;
    --brand-orange: #e8722a;
    --ink: #2b2b2b;
  }
  * { margin: 0; padding: 0; box-sizing: border-box; }
  html, body {
    width: 1200px; height: 1200px; overflow: hidden;
    background: var(--backdrop);
  }
  .card {
    position: absolute; left: 240px; top: 96px;
    width: 720px; height: 1008px; overflow: hidden;
    background: radial-gradient(ellipse at 60% 85%, var(--card-warm) 0%, var(--card-light) 60%);
  }
  .decor { position: absolute; opacity: .75; }
  .decor--poinsettia {
    left: -10px; top: -10px; width: 210px; height: 200px; border-radius: 50%;
    background: radial-gradient(circle at 45% 45%, #f0dcbd 0%, #e8cfa9 50%, rgba(232,207,169,0) 75%);
  }
  .decor--foliage-top {
    right: -20px; top: -20px; width: 320px; height: 320px;
    background: radial-gradient(ellipse at 70% 30%, rgba(214,170,110,.45) 0%, rgba(214,170,110,0) 70%);
  }
  .decor--foliage-bottom {
    left: 0; bottom: 0; width: 720px; height: 230px;
    background: linear-gradient(to top, rgba(210,168,112,.4), rgba(210,168,112,0));
  }
  .decor--star-right {
    right: 30px; bottom: 110px; width: 120px; height: 120px; border-radius: 50%;
    background: radial-gradient(circle, rgba(232,200,155,.8) 0%, rgba(232,200,155,0) 70%);
  }
  .decor--star-left {
    left: 40px; bottom: 200px; width: 70px; height: 70px; border-radius: 50%;
    background: radial-gradient(circle, rgba(232,200,155,.8) 0%, rgba(232,200,155,0) 70%);
  }
  .brand {
    position: absolute; left: 0; right: 0; top: 82px;
    display: flex; justify-content: center; align-items: center; gap: 14px;
  }
  .brand__mark { width: 30px; height: 30px; background: var(--brand-orange); }
  .brand__name {
    font-family: "Open Sans", sans-serif; font-weight: 700;
    font-size: 40px; line-height: 1; color: var(--brand-grey); letter-spacing: -1px;
  }
  .greeting {
    position: absolute; font-family: "Great Vibes", cursive; font-weight: 400;
    color: var(--script-brown); line-height: 1; white-space: nowrap;
  }
  .greeting--first { left: 0; right: 0; top: 196px; text-align: center; font-size: 100px; }
  .greeting--second { left: 290px; top: 300px; font-size: 92px; }
  .year {
    position: absolute; left: 0; right: 0; top: 431px; height: 236px;
    text-align: center; font-family: "Archivo Black", sans-serif;
    font-size: 236px; line-height: 236px; letter-spacing: -6px;
    transform: scaleX(0.72); transform-origin: center;
  }
  .year__outline {
    position: absolute; left: 0; right: 0; top: -22px;
    color: transparent; -webkit-text-stroke: 2px var(--year-red);
  }
  .year__fill { position: relative; color: var(--year-red); }
  .device {
    position: absolute; left: 303px; top: 674px; width: 159px; height: 261px;
    border-radius: 70px 70px 30px 30px;
    background: linear-gradient(180deg, #e6e6ea 0%, #c9c9cf 100%);
  }
  .website {
    position: absolute; left: 0; right: 0; top: 942px; text-align: center;
    font-family: "Roboto Condensed", sans-serif; font-weight: 500;
    font-size: 26px; line-height: 1.3; color: var(--ink);
  }
  .website span { background: rgba(255,255,255,.85); padding: 2px 8px; border-radius: 6px; }
</style>
</head>
<body>
  <main class="card">
    <div class="decor decor--poinsettia" role="img" aria-label="Cream watercolour poinsettia flower"></div>
    <div class="decor decor--foliage-top" role="img" aria-label="Golden line-art fern and leaf foliage"></div>
    <div class="decor decor--foliage-bottom" role="img" aria-label="Golden line-art leaves and glitter along the bottom"></div>
    <div class="decor decor--star-right" role="img" aria-label="Paper star ornament"></div>
    <div class="decor decor--star-left" role="img" aria-label="Small paper star ornament"></div>

    <header class="brand">
      <span class="brand__mark"></span>
      <span class="brand__name">Varden Clinical</span>
    </header>

    <h1>
      <span class="greeting greeting--first">Happy New</span>
      <span class="greeting greeting--second">Year</span>
    </h1>

    <div class="year" aria-label="2022">
      <span class="year__outline" aria-hidden="true">2022</span>
      <span class="year__fill">2022</span>
    </div>

    <div class="device" role="img" aria-label="Photo of the white neck-worn therapy device with mouthpiece and cable"></div>

    <p class="website"><span>www.vardenclinical.com</span></p>
  </main>
</body>
</html>
```